Creation of a Velmaro website

Velmaro is a company% 26 # 233; t% 26 # 233; consulting that accompanies Swiss companies or% 26 # 233; strang% 26 # 232; res in the d% 26 # 233; development of their business on the market% 26 # 233; Switzerland by providing strategic contacts (personalized contact program% 26 # 233; s) or market information% 26 # 233; (% 26 # 233; market research% 26 # 233;) and by providing administrative support (repr% 26 # 233; tax representation) or logistics (organization of% 26 # 233; v% 26 # 233; nement, assistance for participation% 26 # 224; fairs). Our customers are mainly European companies wishing to develop their business in Switzerland. N% 26 # 233; however, our services are% 26 # 233; also aimed at Swiss companies wishing to develop in other parts of Switzerland. Our site must therefore be% 26 # 234; capable of being translated into several languages. The services offered% 26 # 233; s by Velmaro may also% 26 # 233; also% 26 # 39;% 26 # 233; tender% 26 # 224; promoting tourism in Switzerland for countries or regions% 26 # 233; foreigners or% 26 # 224; the promotion of trade fairs or fairs with% 26 # 232; sd% 26 # 39; companies of the sectors concerned% 26 # 233; s. It is therefore n% 26 # 233; necessary to be able to add sub-headings of services which can% 26 # 234; be displayed% 26 # 233; es or hide% 26 # 233; es as required. We are 2 associates% 26 # 233; s, low% 26 # 233; s in the French-speaking parts (Neuch% 26 # 226; tel) and al% 26 # 233; manique (Zurich) of Switzerland.

Target Market(s)

Swiss or European companies wishing to develop their activities in Switzerland.

Coding

Coded - Design and coding required

Colors

Designer to choose colors to be used in the design.

Requirements
Must have
• A home page A section of% 26 # 233; writing the services offered% 26 # 233; es by Velmaro with the possibility% 26 # 233; d% 26 # 39; add sub-headings which can% 26 # 234; be displayed% 26 # 233; e or hidden% 26 # 233; e A page with the r% 26 # 233; f% 26 # 233; which can be displayed% 26 # 233; e or hidden% 26 # 233; e A page of% 26 # 233; writing l% 26 # 39;% 26 # 233; team A page with form contact, addresses and int card% 26 # 233; gr% 26 # 233; e The site must% 26 # 234; be low% 26 # 233; on a CMS allowing% 26 # 39;% 26 # 234; to be autonomous in modifying the website The possibility% 26 # 233; to be able to translate the site into several languages (FR, EN, DE, IT, NL, ...)

```html
<!DOCTYPE html>
<html lang="en">
<head>
<meta charset="utf-8">
<title>Velmaro</title>
<link rel="stylesheet" href="https://fonts.googleapis.com/css2?family=Roboto:wght@300;400;500;700&family=Allura&display=swap">
<style>
:root{
  --navy:#1a2b40;
  --navy-deep:#14202f;
  --slate:#a3afc4;
  --search:#9aa8bd;
  --text:#3a3f47;
  --white:#ffffff;
  --line:#d5d9e0;
}
*{box-sizing:border-box;margin:0;padding:0}
html,body{width:1200px;height:3712px;overflow:hidden}
body{position:relative;background:var(--white);font-family:'Roboto',sans-serif;color:var(--text)}
.abs{position:absolute}
.center{left:0;width:1200px;text-align:center}

/* photo areas */
.photo-hero{top:0;left:0;width:1200px;height:910px;background:linear-gradient(135deg,#5a4636 0%,#8a7462 35%,#b9aa98 55%,#6f6152 80%,#3e342c 100%)}
.photo-testimonial{top:1350px;left:0;width:1200px;height:640px;background:linear-gradient(180deg,#1d2c44 0%,#2a3d5c 45%,#3a567c 75%,#22344f 100%)}
.photo-touch{top:2540px;left:0;width:1200px;height:630px;background:linear-gradient(135deg,#2b3f5c 0%,#4a6282 40%,#5f7797 60%,#2e4361 100%)}
.shapes{top:0;left:0;width:1200px;height:3712px;pointer-events:none}

/* header */
.brand{display:flex;align-items:center;gap:16px}
.brand-square{width:44px;height:44px;border-radius:10px;background:var(--navy)}
.brand-name{font-size:40px;font-weight:300;letter-spacing:4px;color:var(--navy);text-transform:uppercase}
.header-brand{top:40px;left:122px}
.lang{top:48px;left:967px;width:118px;height:38px;border:1px solid var(--navy);background:#fff;display:flex;align-items:center;padding:0 12px;font-size:13px;gap:8px;color:var(--navy)}
.flag{width:22px;height:14px;background:linear-gradient(#c8102e,#c8102e) center/100% 3px no-repeat,linear-gradient(#c8102e,#c8102e) center/3px 100% no-repeat,#012169}
.lang svg{margin-left:auto}
.nav{top:118px;left:112px;width:800px;height:62px;background:var(--navy);display:flex;align-items:center;padding-left:34px;gap:30px}
.nav a{color:#fff;text-decoration:none;font-size:13.5px;font-weight:500;text-transform:uppercase}
.search{top:118px;left:912px;width:176px;height:62px;background:var(--search);display:flex;align-items:center;justify-content:space-between;padding:0 30px 0 33px;color:#fff;font-size:13.5px;text-transform:uppercase}

.chev{width:36px;height:36px;border-radius:50%;background:#fff;display:flex;align-items:center;justify-content:center;box-shadow:0 2px 6px rgba(0,0,0,.12)}
.mark{width:58px;height:58px;border-radius:12px;background:var(--navy);left:571px}

/* welcome */
.welcome-title{top:930px;font-size:62px;font-weight:700;color:var(--navy)}
.welcome-title span{color:var(--slate)}
.welcome-text{top:1028px;left:155px;width:890px;text-align:center;font-size:16px;line-height:25.8px;font-weight:300;color:var(--text)}
.btn{height:44px;border:2px solid var(--navy);border-radius:22px;background:#fff;color:var(--navy);font-weight:700;font-size:15px;display:flex;align-items:center;justify-content:center;box-shadow:0 8px 14px rgba(0,0,0,.1);text-transform:uppercase}

/* testimonials */
.section-title{font-size:40px;font-weight:500;color:var(--navy)}
.quote{top:1544px;left:255px;width:690px;text-align:center;color:#fff;font-size:17.5px;line-height:25.8px}
.author{top:1696px;color:#fff;font-family:'Allura',cursive;font-size:40px}
.dots{top:1786px;display:flex;justify-content:center;gap:17px}
.dot{width:9px;height:9px;background:rgba(255,255,255,.6);transform:rotate(45deg)}
.dot.on{background:#fff;width:11px;height:11px}

/* services */
.service{width:310px;text-align:center}
.service svg{display:block;margin:0 auto}
.service h3{font-size:24px;font-weight:500;color:var(--navy);margin-top:14px}
.service p{font-size:12px;line-height:20.6px;margin-top:12px;color:var(--text)}

/* touch */
.touch-title{top:2816px;font-size:40px;font-weight:700;color:#fff}
.touch-text{top:2886px;left:245px;width:710px;text-align:center;font-size:17.5px;line-height:25.8px;color:#e8edf4;font-weight:300}
.form-card{top:3003px;left:222px;width:756px;height:366px;background:#fff;box-shadow:0 6px 18px rgba(0,0,0,.08)}
.field{border:1px solid var(--line);border-radius:19px;height:38px;display:flex;align-items:center;justify-content:space-between;padding:0 24px;font-size:13.5px;color:#333}
.field.message{border-radius:6px;height:124px;align-items:flex-start;padding-top:16px}
.after-text{top:3400px;left:240px;width:720px;text-align:center;font-size:15.5px;line-height:25.8px;font-weight:300}
.social{width:58px;height:58px;border-radius:50%;border:2px solid var(--navy);background:#fff;box-shadow:0 6px 12px rgba(0,0,0,.12)}
.social.active{background:#0f2f73;border-color:#0f2f73}

/* footer */
.footer{top:3606px;left:0;width:1200px;height:106px;background:var(--navy-deep)}
.footer .brand-square{background:#fff}
.footer .brand-name{color:#fff}
.copyright{top:3650px;left:895px;color:#fff;font-size:11.5px}
</style>
</head>
<body>

<div class="abs photo-hero" role="img" aria-label="Photo of a business presentation in a modern office with colleagues watching a chart on a screen"></div>
<div class="abs photo-testimonial" role="img" aria-label="Photo of freight transport: cargo plane, truck and container terminal at dusk, tinted navy"></div>
<div class="abs photo-touch" role="img" aria-label="Photo of cheerful business partners giving a high five, tinted blue"></div>

<svg class="abs shapes" viewBox="0 0 1200 3712" aria-hidden="true">
  <g fill="#ffffff">
    <path d="M0 0H1200V90Q600 150 0 90Z"/>
    <path d="M0 900Q600 700 1200 900V915H0Z"/>
    <path d="M0 1340H1200V1362Q600 1534 0 1362Z"/>
    <path d="M0 1981Q600 1765 1200 1981V2000H0Z"/>
    <path d="M0 2530H1200V2547Q600 2727 0 2547Z"/>
    <path d="M0 3166Q600 2914 1200 3166V3180H0Z"/>
  </g>
</svg>

<header>
  <div class="abs brand header-brand"><div class="brand-square"></div><span class="brand-name">Velmaro</span></div>
  <div class="abs lang"><span class="flag"></span>En
    <svg width="10" height="6" viewBox="0 0 10 6"><path d="M1 1l4 4 4-4" fill="none" stroke="#1a2b40" stroke-width="1.8"/></svg>
  </div>
  <nav class="abs nav"><a>Home</a><a>About</a><a>Services</a><a>Testimonials</a><a>Contact Us</a></nav>
  <div class="abs search">Search
    <svg width="13" height="13" viewBox="0 0 14 14"><circle cx="6" cy="6" r="4.5" fill="none" stroke="#fff" stroke-width="2"/><path d="M9.5 9.5L13 13" stroke="#fff" stroke-width="2"/></svg>
  </div>
</header>

<div class="abs chev" style="top:782px;left:582px"><svg width="10" height="6" viewBox="0 0 10 6"><path d="M1 1l4 4 4-4" fill="none" stroke="#1a2b40" stroke-width="1.8"/></svg></div>

<section class="welcome">
  <div class="abs mark" style="top:861px"></div>
  <h1 class="abs center welcome-title"><span>Welcome To</span> Velmaro</h1>
  <p class="abs welcome-text">Velmaro is a company consulting that accompanies Swiss companies or strangers in the development of their business on the market Switzerland by providing strategic contacts (personalized contact program s) or market information ( market research) and by providing administrative support (repr tax representation) or logistics (organization of v nement, assistance for participation fairs). Our customers are mainly European companies wishing to develop their business in Switzerland. N however, our services are also aimed at Swiss companies wishing to develop in other parts of Switzerland.</p>
  <div class="abs btn" style="top:1193px;left:533px;width:134px">Read More</div>
</section>

<section class="testimonials">
  <div class="abs mark" style="top:1292px"></div>
  <h2 class="abs center section-title" style="top:1374px">Testimonials</h2>
  <div class="abs chev" style="top:1440px;left:582px"><svg width="10" height="6" viewBox="0 0 10 6"><path d="M1 1l4 4 4-4" fill="none" stroke="#1a2b40" stroke-width="1.8"/></svg></div>
  <p class="abs quote">Sed ut perspiciatis unde omnis iste natus error sit voluptatem accusantium doloremque laudantium, totam rem aperiam, eaque ipsa quae ab illo inventore veritatis et quasi architecto beatae vitae dicta sunt explicabo. Nemo enim ipsam voluptatem quia voluptas sit aspernatur aut odit aut fugit, sed quia consequuntur magni dolores eos qui ratione voluptatem sequi nesciunt.</p>
  <div class="abs center author">- Lenora</div>
  <div class="abs center dots"><span class="dot"></span><span class="dot"></span><span class="dot"></span><span class="dot"></span><span class="dot on"></span><span class="dot"></span><span class="dot"></span><span class="dot"></span><span class="dot"></span><span class="dot"></span></div>
</section>

<div class="abs chev" style="top:1855px;left:582px"><svg width="10" height="6" viewBox="0 0 10 6"><path d="M1 1l4 4 4-4" fill="none" stroke="#1a2b40" stroke-width="1.8"/></svg></div>

<section class="services">
  <div class="abs mark" style="top:1925px"></div>
  <h2 class="abs center section-title" style="top:2008px">Our Services</h2>

  <div class="abs service" style="top:2128px;left:107px">
    <svg width="96" height="96" viewBox="0 0 96 96" fill="none" stroke="#1a2b40" stroke-width="3">
      <circle cx="38" cy="40" r="30"/><path d="M60 62l24 24" stroke-width="6"/>
      <path d="M24 58V44M32 58V38M40 58V34M48 58V42" /><path d="M18 40l14-10 10 6 20-20" /><path d="M54 16h8v8"/>
    </svg>
    <h3>Market Research</h3>
    <p>Sed ut perspiciatis unde omnis iste natus error sit voluptatem accusantium doloremque laudantium, totam rem aperiam, eaque ipsa quae ab illo inventore veritatis et quasi architecto beatae vitae dicta sunt explicabo. Nemo enim ipsam voluptatem.</p>
  </div>

  <div class="abs service" style="top:2128px;left:447px">
    <svg width="96" height="96" viewBox="0 0 96 96" fill="none" stroke="#1a2b40" stroke-width="3">
      <circle cx="48" cy="18" r="15"/><path d="M53 11c-2-3-10-3-10 2s10 3 10 8-8 5-10 2M48 7v22"/>
      <path d="M48 33v18M18 51h60M18 51v14M48 51v14M78 51v14"/>
      <circle cx="18" cy="76" r="11"/><circle cx="48" cy="76" r="11"/><circle cx="78" cy="76" r="11"/>
    </svg>
    <h3>Tax Representation</h3>
    <p>Sed ut perspiciatis unde omnis iste natus error sit voluptatem accusantium doloremque laudantium, totam rem aperiam, eaque ipsa quae ab illo inventore veritatis et quasi architecto beatae vitae dicta sunt explicabo. Nemo enim ipsam voluptatem.</p>
  </div>

  <div class="abs service" style="top:2128px;left:783px">
    <svg width="96" height="96" viewBox="0 0 96 96" fill="none" stroke="#1a2b40" stroke-width="3">
      <path d="M10 70V44h36V16H22v28"/><path d="M46 44l14 8v18H10"/><path d="M72 8v70h20"/>
      <circle cx="20" cy="76" r="8"/><circle cx="52" cy="76" r="8"/>
    </svg>
    <h3>Logistics</h3>
    <p>Sed ut perspiciatis unde omnis iste natus error sit voluptatem accusantium doloremque laudantium, totam rem aperiam, eaque ipsa quae ab illo inventore veritatis et quasi architecto beatae vitae dicta sunt explicabo. Nemo enim ipsam voluptatem.</p>
  </div>

  <div class="abs btn" style="top:2443px;left:511px;width:178px">More Services</div>
</section>

<section class="touch">
  <h2 class="abs center touch-title">Get in Touch</h2>
  <p class="abs touch-text">Sed ut perspiciatis unde omnis iste natus error sit voluptatem accusantium doloremque laudantium, totam rem aperiam, eaque ipsa quae ab illo inventore veritatis et quasi architecto beatae vitae dicta sunt explicabo.</p>
  <form class="abs form-card">
    <div class="abs field" style="top:60px;left:83px;width:287px">First Name
      <svg width="13" height="13" viewBox="0 0 14 14" fill="none" stroke="#333" stroke-width="1.4"><circle cx="7" cy="4.5" r="3"/><path d="M1.5 13c0-3 2.5-5 5.5-5s5.5 2 5.5 5z"/></svg>
    </div>
    <div class="abs field" style="top:60px;left:385px;width:287px">Email
      <svg width="14" height="11" viewBox="0 0 14 11" fill="none" stroke="#333" stroke-width="1.4"><rect x="1" y="1" width="12" height="9"/><path d="M1 1l6 5 6-5"/></svg>
    </div>
    <div class="abs field message" style="top:118px;left:86px;width:586px">Message
      <svg width="13" height="13" viewBox="0 0 14 14"><path d="M2 12l1-4 7-7 3 3-7 7z" fill="#333"/></svg>
    </div>
    <div class="abs btn" style="top:277px;left:311px;width:134px">Submit</div>
  </form>
  <p class="abs after-text">Quis autem vel eum iure reprehenderit qui in ea voluptate velit esse quam nihil molestiae consequatur, vel illum qui dolorem eum fugiat quo voluptas nulla pariatur</p>
  <div class="abs social" style="top:3498px;left:490px" aria-label="Professional network profile"></div>
  <div class="abs social active" style="top:3498px;left:571px" aria-label="Social network page"></div>
  <div class="abs social" style="top:3498px;left:652px" aria-label="Photo sharing profile"></div>
</section>

<footer class="abs footer"></footer>
<div class="abs chev" style="top:3588px;left:582px"><svg width="10" height="6" viewBox="0 0 10 6"><path d="M1 5l4-4 4 4" fill="none" stroke="#1a2b40" stroke-width="1.8"/></svg></div>
<div class="abs brand" style="top:3638px;left:112px"><div class="brand-square"></div><span class="brand-name" style="color:#fff">Velmaro</span></div>
<div class="abs copyright">© 2020 &nbsp;|&nbsp; www.velmaro-consult.ch</div>

</body>
</html>
```